Business Card: RW Office Partners - Your organised problem solver

Business Name: RW Office Partners
Website: www.rwofficepartners.com.au
Email: marisol@rwofficepartners.com.au
Mobile: 61 482 907 236
Facebook: @rwofficepartners
Instrgram: @rwofficepartners

Brading Colours:
HEX
#986474
#ddccd3
#7a8498
#c9d8e4
#000000
#ffffff

Tag Line: Your dependable admin partner

Link to DRAFT website:
https://deskhelpcollective.wixsite.com/rw-office-partners

About Page from the website:
My name is Marisol Wrenfield, and I would love to assist you to become more productive in your day to day and achieve your business and personal goals.
My mission is to give you time, time to work on the important tasks of your business or to be able to spend more time with your family. I will take on the tasks you don’t have time for, don’t know well or simply don’t like to do.
I have an extensive background in Administration, Tender Coordination, Document Control, WHS and Quality Management working primarily in the Construction, Mining and Corporate World.
I am passionate about being organised, having order and making things in your life (and mine) easier! I love to watch something unfold and grow into something amazing! I am known for being the go-to problem solver, the organiser of all things, producing high standards of work even under pressure. I’m also a confident communicator, and I understand that you’re busy running your business.

Target Market(s)

Small to Medium Business who require assistance in their business by a virtual assistant.

Industry/Entity Type

Virtual Assistant

Contact Information for Business Card

Mobile: 61 482 907 236

Font styles to use
Sans Serif

Colors
ffffff

Requirements
Must have
• Branding Colours as outlined.
Contact Details as outlined.
Logo as provided.
Proper contact details - mobile, facebook, instragm, website.
Simple, Elegant, very clean looking.
Should not have
• Note cute with pictures.
Not too girly as still want to market to construction companies.

```html
<!DOCTYPE html>
<html lang="en">
<head>
<meta charset="utf-8">
<title>RW Office Partners – Business Card</title>
<link rel="stylesheet" href="https://fonts.googleapis.com/css2?family=Montserrat:wght@500;600&family=Roboto:wght@400;500&display=swap">
<style>
  :root {
    --mauve: #8d5f6e;
    --mauve-brand: #986474;
    --slate: #7a8498;
    --paper: #ffffff;
    --ink: #333333;
    --backdrop: #e9e7e8;
  }
  * { box-sizing: border-box; margin: 0; padding: 0; }
  html, body { width: 1200px; height: 1200px; overflow: hidden; }
  body {
    background: var(--backdrop);
    font-family: "Roboto", Arial, sans-serif;
    position: relative;
  }
  .card {
    position: absolute;
    left: 244px;
    width: 712px;
    height: 420px;
    border-radius: 26px;
    overflow: hidden;
  }
  .card--front {
    top: 118px;
    background: var(--mauve);
    display: flex;
    align-items: center;
    justify-content: center;
  }
  .card--back {
    top: 642px;
    background: var(--paper);
  }
  .brand-name {
    font-family: "Montserrat", Arial, sans-serif;
    font-weight: 600;
    letter-spacing: 1px;
  }
  .card--front .brand-name {
    color: var(--paper);
    font-size: 54px;
  }
  .card--back .brand-name {
    position: absolute;
    left: 44px;
    top: 62px;
    color: var(--mauve-brand);
    font-size: 44px;
  }
  .tagline {
    position: absolute;
    left: 46px;
    top: 138px;
    font-size: 19px;
    letter-spacing: 3px;
    color: var(--ink);
  }
  .person {
    position: absolute;
    left: 44px;
    top: 214px;
  }
  .person-name {
    font-size: 25px;
    font-weight: 500;
    color: var(--mauve-brand);
  }
  .person-role {
    margin-top: 6px;
    font-size: 17px;
    color: var(--ink);
  }
  .contact-panel {
    position: absolute;
    left: 0;
    top: 0;
  }
  .contact-list {
    position: absolute;
    right: 38px;
    top: 258px;
    list-style: none;
    color: var(--paper);
    font-size: 17px;
    text-align: right;
  }
  .contact-list li {
    display: flex;
    align-items: center;
    justify-content: flex-end;
    gap: 12px;
    height: 26.5px;
  }
  .contact-icon { width: 16px; height: 16px; flex: none; }
</style>
</head>
<body>

<section class="card card--front">
  <p class="brand-name">RW Office Partners</p>
</section>

<section class="card card--back">
  <svg class="contact-panel" width="712" height="420" viewBox="0 0 712 420" aria-hidden="true">
    <polygon points="250,420 350,232 712,232 712,420" fill="var(--mauve)"/>
    <polyline points="228,420 336,218 712,218" fill="none" stroke="var(--slate)" stroke-width="4"/>
  </svg>

  <p class="brand-name">RW Office Partners</p>
  <p class="tagline">Your dependable admin partner</p>

  <div class="person">
    <p class="person-name">Marisol Wrenfield</p>
    <p class="person-role">Virtual Assistant</p>
  </div>

  <ul class="contact-list">
    <li>61 482 907 236
      <svg class="contact-icon" viewBox="0 0 16 16"><path d="M3 4 C3 2 13 2 13 4 L13 6 L10.5 6 L10.5 4.8 L5.5 4.8 L5.5 6 L3 6 Z M4 8 L12 8 L13 13 L3 13 Z" fill="#fff"/></svg>
    </li>
    <li>@rwofficepartners
      <svg class="contact-icon" viewBox="0 0 16 16"><rect x="1.5" y="3.5" width="13" height="9" fill="none" stroke="#fff" stroke-width="1.4"/><path d="M1.5 3.5 L8 9 L14.5 3.5" fill="none" stroke="#fff" stroke-width="1.4"/></svg>
    </li>
    <li>@rwofficepartners
      <svg class="contact-icon" viewBox="0 0 16 16"><circle cx="8" cy="8" r="6.3" fill="none" stroke="#fff" stroke-width="1.3"/><ellipse cx="8" cy="8" rx="2.8" ry="6.3" fill="none" stroke="#fff" stroke-width="1.1"/><path d="M1.7 8 H14.3" stroke="#fff" stroke-width="1.1"/></svg>
    </li>
    <li>www.rwofficepartners.com.au
      <svg class="contact-icon" viewBox="0 0 16 16"><rect x="1.5" y="1.5" width="13" height="13" rx="2.5" fill="#fff"/></svg>
    </li>
    <li>marisol@rwofficepartners.com.au
      <svg class="contact-icon" viewBox="0 0 16 16"><rect x="1.5" y="1.5" width="13" height="13" rx="2.5" fill="#fff"/></svg>
    </li>
  </ul>
</section>

</body>
</html>
```